Rollers & Glides.com

Vertical Business Card with focus on branding with our icon. Information on card will be logo, persons name, position, phone number, email address and website. Use the the name Marcus Pellow, position President, phone number 480.915.2267, email Marcus@rollersandglides-demo.com, website www.rollersandglides-demo.com.

```html
<!DOCTYPE html>
<html lang="en">
<head>
<meta charset="utf-8">
<title>Rollers &amp; Glides.com — Business Card</title>
<link rel="stylesheet" href="https://fonts.googleapis.com/css2?family=Roboto:wght@500&family=Arimo:wght@400;700&display=swap">
<style>
  :root {
    --brand-blue: #3360ad;
    --paper-white: #ffffff;
    --backdrop: #2a2a2a;
    --shadow: rgba(0, 0, 0, 0.45);
  }
  * { box-sizing: border-box; margin: 0; padding: 0; }
  html, body {
    width: 1200px;
    height: 1015px;
    overflow: hidden;
    background: var(--backdrop);
  }
  .canvas {
    width: 1200px;
    height: 1015px;
    display: flex;
    flex-direction: column;
    align-items: center;
    justify-content: center;
    gap: 56px;
  }
  .card {
    width: 700px;
    height: 400px;
    box-shadow: 0 14px 34px var(--shadow);
    position: relative;
    overflow: hidden;
  }
  /* Back of card */
  .card-back {
    background: var(--brand-blue);
    display: flex;
    flex-direction: column;
    align-items: center;
    justify-content: center;
    gap: 26px;
  }
  .brand-mark {
    width: 92px;
    height: 92px;
    border-radius: 50%;
    border: 14px solid var(--paper-white);
  }
  .brand-name {
    font-family: "Roboto", sans-serif;
    font-weight: 500;
    font-size: 38px;
    letter-spacing: 2px;
    color: var(--paper-white);
  }
  /* Front of card */
  .card-front {
    display: grid;
    grid-template-columns: 53% 47%;
    background: var(--paper-white);
  }
  .contact-panel {
    background: var(--brand-blue);
    color: var(--paper-white);
    font-family: "Arimo", sans-serif;
    padding: 110px 0 0 54px;
  }
  .person-name {
    font-weight: 700;
    font-size: 25px;
    text-transform: uppercase;
    line-height: 1;
  }
  .person-role {
    font-size: 19px;
    margin-top: 4px;
  }
  .contact-list {
    list-style: none;
    margin-top: 46px;
    display: flex;
    flex-direction: column;
    gap: 7px;
  }
  .contact-item {
    display: flex;
    align-items: center;
    gap: 10px;
    font-size: 15.5px;
    white-space: nowrap;
  }
  .contact-icon {
    width: 16px;
    height: 16px;
    flex: none;
  }
  .brand-panel {
    display: flex;
    flex-direction: column;
    align-items: center;
    justify-content: center;
    gap: 20px;
    padding-bottom: 20px;
  }
  .brand-panel .brand-mark {
    width: 62px;
    height: 62px;
    border-width: 10px;
    border-color: var(--brand-blue);
  }
  .brand-panel .brand-name {
    font-size: 23px;
    letter-spacing: 1.2px;
    color: var(--brand-blue);
  }
</style>
</head>
<body>
<main class="canvas">
  <section class="card card-back" aria-label="Card back">
    <span class="brand-mark" aria-hidden="true"></span>
    <p class="brand-name">Rollers &amp; Glides.com</p>
  </section>

  <section class="card card-front" aria-label="Card front">
    <div class="contact-panel">
      <h1 class="person-name">Marcus Pellow</h1>
      <p class="person-role">President</p>
      <ul class="contact-list">
        <li class="contact-item">
          <svg class="contact-icon" viewBox="0 0 24 24" aria-hidden="true"><path fill="#fff" d="M6.6 10.8a15 15 0 0 0 6.6 6.6l2.2-2.2c.3-.3.7-.4 1-.2 1.1.4 2.3.6 3.6.6.6 0 1 .4 1 1V20c0 .6-.4 1-1 1A17 17 0 0 1 3 4c0-.6.4-1 1-1h3.5c.6 0 1 .4 1 1 0 1.3.2 2.5.6 3.6.1.3 0 .7-.2 1z"/></svg>
          480.915.2267
        </li>
        <li class="contact-item">
          <svg class="contact-icon" viewBox="0 0 24 24" aria-hidden="true"><rect x="2" y="5" width="20" height="14" fill="#fff"/><path d="M2 5l10 8 10-8" fill="none" stroke="#3360ad" stroke-width="1.8"/></svg>
          Marcus@rollersandglides-demo.com
        </li>
        <li class="contact-item">
          <svg class="contact-icon" viewBox="0 0 24 24" aria-hidden="true"><g fill="none" stroke="#fff" stroke-width="1.8"><circle cx="12" cy="12" r="10"/><ellipse cx="12" cy="12" rx="4.5" ry="10"/><path d="M2 12h20M4 7h16M4 17h16"/></g></svg>
          www.rollersandglides-demo.com
        </li>
      </ul>
    </div>
    <div class="brand-panel">
      <span class="brand-mark" aria-hidden="true"></span>
      <p class="brand-name">Rollers &amp; Glides.com</p>
    </div>
  </section>
</main>
</body>
</html>
```